Every Shelf Set Neatly or ESN Organized needs a business card design. ESN Organized is a professi

We need a business card design that is clean, sharp and conveys a sense of organization. I already have a logo.

Target Market(s)

Families (specifically mothers), small business owners, parents, seniors

Industry/Entity Type

Business

Contact Information for Business Card

My website is www.esnorganized-example.com and my Facebook page is http://www.sociallink-example.com/everyshelfsetneatly. The phone number is 418-552-7094 and I want to be listed as Lorna M. Pelham, Owner

Requirements
Must have
• My logo.

```html
<!DOCTYPE html>
<html lang="en">
<head>
<meta charset="utf-8">
<title>Every Shelf Set Neatly – Business Card</title>
<link rel="stylesheet" href="https://fonts.googleapis.com/css2?family=Montserrat:wght@500&family=Roboto:ital,wght@0,400;0,500;0,700;1,700&display=swap">
<style>
  :root {
    --page-bg: #d8d5d1;
    --card-bg: #eef0f2;
    --brand-blue: #1f55b8;
    --brand-blue-deep: #163f96;
    --ink: #2b2d31;
    --ink-soft: #55585e;
    --rule: #b9bcc1;
  }
  * { margin: 0; padding: 0; box-sizing: border-box; }
  html, body {
    width: 1200px; height: 969px; overflow: hidden;
    background: var(--page-bg);
  }
  .canvas { position: relative; width: 1200px; height: 969px; }
  .card {
    position: absolute; left: 100px; top: 200px;
    width: 1000px; height: 570px;
    background: var(--card-bg);
    overflow: hidden;
    box-shadow: 0 10px 30px rgba(0,0,0,0.18);
    font-family: "Roboto", Arial, sans-serif;
  }
  .clip-art { position: absolute; inset: 0; width: 1000px; height: 570px; }
  .brand {
    position: absolute; left: 58px; top: 62px;
    display: flex; align-items: center; gap: 16px;
  }
  .brand-mark { width: 34px; height: 34px; background: var(--brand-blue); }
  .brand-name {
    font-family: "Montserrat", Arial, sans-serif; font-weight: 500;
    font-size: 38px; color: var(--ink); letter-spacing: 1px;
  }
  .person-name {
    position: absolute; left: 60px; top: 170px;
    font-size: 38px; font-weight: 700; color: var(--brand-blue);
    letter-spacing: 0.5px; text-transform: uppercase;
  }
  .person-role {
    position: absolute; left: 62px; top: 223px;
    font-size: 27px; font-weight: 500; color: var(--ink);
  }
  .rule {
    position: absolute; left: 62px; width: 205px; height: 2px;
    background: var(--rule);
  }
  .rule-top { top: 272px; }
  .rule-bottom { top: 400px; }
  .contact {
    position: absolute; left: 62px;
    display: flex; align-items: center; gap: 12px;
    font-size: 27px; color: var(--ink-soft);
  }
  .contact-phone { top: 306px; }
  .contact-social { top: 346px; }
  .contact-icon { width: 26px; height: 26px; flex: none; }
  .social-square { width: 24px; height: 24px; background: var(--brand-blue-deep); flex: none; }
  .website {
    position: absolute; left: 62px; top: 420px;
    font-size: 27px; font-weight: 500; color: var(--brand-blue);
    letter-spacing: 1.5px;
  }
  .tagline {
    position: absolute; left: 62px; top: 460px;
    font-size: 26px; font-weight: 700; font-style: italic;
    color: var(--ink-soft); line-height: 38px;
  }
</style>
</head>
<body>
<div class="canvas">
  <div class="card">
    <svg class="clip-art" viewBox="0 0 1000 570" role="img" aria-label="Large blue paperclip illustration">
      <defs>
        <linearGradient id="clipBlue" x1="0" y1="1" x2="1" y2="0">
          <stop offset="0" stop-color="#1f55b8"/>
          <stop offset="1" stop-color="#163f96"/>
        </linearGradient>
      </defs>
      <path d="M900 0 L1000 0 L1000 570 L650 570 C575 560 545 485 580 430 Z" fill="url(#clipBlue)"/>
    </svg>

    <div class="brand">
      <span class="brand-mark"></span>
      <span class="brand-name">Every Shelf Set Neatly</span>
    </div>

    <div class="person-name">Lorna M. Pelham</div>
    <div class="person-role">Owner</div>
    <div class="rule rule-top"></div>

    <div class="contact contact-phone">
      <svg class="contact-icon" viewBox="0 0 24 24" aria-hidden="true">
        <path fill="#163f96" d="M6.6 10.8a15.1 15.1 0 0 0 6.6 6.6l2.2-2.2a1 1 0 0 1 1-.25 11.4 11.4 0 0 0 3.6.57 1 1 0 0 1 1 1V20a1 1 0 0 1-1 1A17 17 0 0 1 3 4a1 1 0 0 1 1-1h3.5a1 1 0 0 1 1 1c0 1.25.2 2.45.57 3.57a1 1 0 0 1-.25 1z"/>
      </svg>
      <span>418-552-7094</span>
    </div>
    <div class="contact contact-social">
      <span class="social-square"></span>
      <span>everyshelfsetneatly</span>
    </div>
    <div class="rule rule-bottom"></div>

    <div class="website">www.esnorganized-example.com</div>
    <div class="tagline">Every item in its proper place, every day<br>and every room at ease</div>
  </div>
</div>
</body>
</html>
```